Urgent Cardiac Consult Request

We need a one page (1/2 pg size) order form for Urgent Cardiac Consults so that Emergency depts and walk -in clinics can fill this out and send forms with patient to our office. The page needs to have clear information, easy to read and to fill out. Our logo and address at the top and on the back side a map showing our location. I am sending a version that I have but the doctors want something different in the way of layout.
They want less information on them. At top - options for exam s: Excercise Stress Echo; Echocardiogram; Holter/Loop recorder (3day / 14 day/ other __); Concsult. Pt info in middle . Bottom : Indication s 1) Chest Pain/SOB 2: Palpatations 3) Other_____ Eyecatching, larger logo, etc Thanks

```html
<!DOCTYPE html>
<html lang="en">
<head>
<meta charset="utf-8">
<title>Urgent Cardiac Referral Form</title>
<link href="https://fonts.googleapis.com/css2?family=Oswald:wght@500;600&family=Roboto:ital,wght@0,400;0,500;0,700;1,400;1,500&display=swap" rel="stylesheet">
<style>
  :root {
    --backdrop: #15599c;
    --paper: #ebebed;
    --navy: #123d6e;
    --red: #9c1b22;
    --ink: #2a2a2a;
    --rule: #555;
    --pill: #d4d4d8;
    --map-base: #cfcfd3;
  }
  * { box-sizing: border-box; margin: 0; padding: 0; }
  html, body { width: 1200px; height: 1062px; overflow: hidden; }
  body {
    background: var(--backdrop);
    font-family: "Roboto", Arial, sans-serif;
    color: var(--ink);
    position: relative;
  }
  .sheet {
    position: absolute;
    background: var(--paper);
    overflow: hidden;
  }
  .sheet--front { left: 144px; top: 241px; width: 418px; height: 575px; }
  .sheet--back { left: 632px; top: 238px; width: 420px; height: 578px; }
  .abs { position: absolute; }

  /* front */
  .title-band { left: 136px; top: 0; width: 282px; height: 38px; }
  .title-band svg { position: absolute; inset: 0; }
  .title-band span {
    position: absolute; right: 11px; top: 5px;
    font-family: "Oswald", sans-serif; font-weight: 500;
    font-size: 19px; line-height: 26px; color: #fff;
    letter-spacing: -0.2px; white-space: nowrap;
  }
  .brand { left: 22px; top: 40px; width: 182px; text-align: center; color: var(--navy); font-weight: 700; }
  .brand__mark { width: 30px; height: 30px; border-radius: 50%; background: var(--red); margin: 0 auto 8px; }
  .brand__name { font-size: 19px; letter-spacing: .5px; line-height: 1.05; white-space: nowrap; }
  .brand__sub { font-size: 14px; letter-spacing: 2px; }

  .appointment { left: 254px; top: 74px; width: 146px; }
  .appointment h3 {
    font-family: "Oswald", sans-serif; font-weight: 500; color: var(--navy);
    font-size: 16px; text-align: right; line-height: 1; margin-bottom: 3px; white-space: nowrap;
  }
  .appointment .pill {
    height: 12px; border-radius: 6px; background: var(--pill);
    font-size: 9px; font-weight: 500; padding-left: 6px; line-height: 12px;
    margin-bottom: 5px; letter-spacing: .6px; position: relative;
  }
  .pill .slashes { position: absolute; left: 72px; word-spacing: 28px; }

  .office { top: 150px; display: flex; gap: 6px; font-size: 9px; line-height: 11.5px; white-space: nowrap; }
  .office--a { left: 16px; }
  .office--b { left: 237px; }
  .office b.city { color: var(--red); letter-spacing: .6px; }
  .office .hours { color: var(--navy); font-weight: 700; }
  .office .addr { font-weight: 500; }

  .box {
    display: inline-block; width: 11px; height: 11px;
    border: 1.5px solid var(--navy); border-radius: 2px; flex: none;
  }
  .section-bar {
    left: 14px; width: 394px; height: 17px; background: var(--navy);
    color: #fff; font-weight: 700; font-size: 11.5px; letter-spacing: .8px;
    padding-left: 8px; line-height: 17px; white-space: nowrap;
  }
  .choice { display: flex; align-items: flex-start; gap: 6px; font-size: 10.5px; white-space: nowrap; }
  .choice small { display: block; font-style: italic; font-size: 8.5px; margin-top: 1px; }

  .field-row { left: 24px; right: 20px; display: flex; align-items: flex-end; gap: 6px; font-size: 10px; white-space: nowrap; }
  .field-row .line { flex: 1; border-bottom: 1px solid var(--rule); height: 1px; margin-bottom: 2px; }

  .footer-band {
    left: 0; bottom: 0; width: 100%; height: 21px; background: var(--red);
    color: #fff; font-style: italic; font-weight: 400; font-size: 8.4px;
    line-height: 21px; text-align: center; white-space: nowrap;
  }

  /* back */
  .locations-tag {
    left: 0; top: 29px; width: 156px; height: 19px; background: var(--red);
    color: #fff; font-weight: 700; font-size: 15px; letter-spacing: 3.5px;
    padding-left: 22px; line-height: 19px; white-space: nowrap;
  }
  .back-brand { left: 288px; top: 22px; width: 96px; text-align: center; color: var(--navy); font-weight: 700; font-size: 11px; line-height: 1.2; }
  .back-brand .brand__mark { width: 36px; height: 36px; margin-bottom: 6px; }
  .site-heading { left: 27px; font-weight: 700; font-size: 14px; line-height: 15px; color: #222; white-space: nowrap; }
  .map {
    left: 22px; width: 240px; height: 170px; border-radius: 8px;
    background: linear-gradient(160deg, #d9d9dc 0%, var(--map-base) 60%, #c5c8c6 100%);
  }
  .site-info { left: 262px; width: 158px; text-align: center; color: #222; }
  .site-info svg { display: block; margin: 0 auto 14px; }
  .site-info .addr { font-size: 13.5px; line-height: 16px; }
  .site-info .city { font-size: 14.5px; font-weight: 700; margin-top: 28px; line-height: 18px; }
  .back-rule { left: 0; top: 538px; width: 100%; height: 18px; background: var(--navy); }
</style>
</head>
<body>

<section class="sheet sheet--front">
  <div class="abs title-band">
    <svg width="282" height="38" viewBox="0 0 282 38"><path d="M0 0H282V38H34Q26 38 20 32Z" fill="var(--red)"/></svg>
    <span>URGENT CARDIC REFERRAL FORM</span>
  </div>

  <div class="abs brand">
    <div class="brand__mark"></div>
    <div class="brand__name">LAKESHORE HEART</div>
    <div class="brand__sub">CENTRE</div>
  </div>

  <div class="abs appointment">
    <h3>APPOINTMENT</h3>
    <div class="pill">DATE <span class="slashes">/ /</span></div>
    <div class="pill">TIME</div>
  </div>

  <div class="abs office office--a">
    <span class="box"></span>
    <div>
      <b class="city">BAYFORD :</b> <span class="addr">555-014-2290</span><br>
      <span class="addr">1820 Maple Avenue, Suite 304, Bayford</span><br>
      <span class="hours">Monday - Saturday : 8am-5pm</span>
    </div>
  </div>
  <div class="abs office office--b">
    <span class="box"></span>
    <div>
      <b class="city">MILLBROOK :</b> <span class="addr">555-018-7716</span><br>
      <span class="addr">92 Harbour Street North, Millbrook, ON</span><br>
      <span class="hours">Monday - Friday: 8am - 4pm</span>
    </div>
  </div>

  <div class="abs section-bar" style="top:201px">EXCERCISE</div>
  <div class="abs choice" style="left:24px;top:228px"><span class="box"></span>Stress Echo</div>
  <div class="abs choice" style="left:124px;top:228px"><span class="box"></span>Echocardiogram</div>
  <div class="abs choice" style="left:246px;top:228px"><span class="box"></span><div>Holter/Loop recorder<small>(3day / 14 day/ other ______)</small></div></div>

  <div class="abs section-bar" style="top:265px">PATIENT INFORMATION</div>
  <div class="abs field-row" style="top:291px">Full Name:<span class="line"></span></div>
  <div class="abs field-row" style="top:316px">Date of Birth:<span class="line"></span>&nbsp;Gender <span class="box"></span> Male <span class="box"></span> Female</div>
  <div class="abs field-row" style="top:340px">Health Card#:<span class="line"></span></div>
  <div class="abs field-row" style="top:363px">Phone:<span class="line"></span>&nbsp;Version<span class="line" style="flex:.75"></span></div>

  <div class="abs section-bar" style="top:392px">PHYSICIAN INFORMATION</div>
  <div class="abs field-row" style="top:419px">Physician Name:<span class="line"></span>&nbsp;Billing #:<span class="line" style="flex:.25"></span></div>
  <div class="abs field-row" style="top:443px">Phone:<span class="line"></span>&nbsp;Fax:<span class="line"></span></div>
  <div class="abs field-row" style="top:469px">Ordering Physician Signature:<span class="line"></span>&nbsp;Date:<span class="line"></span></div>

  <div class="abs section-bar" style="top:498px;width:392px">INDICATIONS</div>
  <div class="abs field-row" style="top:526px">
    <span class="box"></span>Chest Pain/SOB&nbsp;&nbsp;
    <span class="box"></span>Palpatations&nbsp;&nbsp;
    <span class="box"></span>Other&nbsp;<span class="line"></span>
  </div>

  <div class="abs footer-band">PLEASE PROVIDE A COMPLETE LIST OF MEDICATIONS AT TIME OF TESTING AND/OR CONSULTATION.</div>
</section>

<section class="sheet sheet--back">
  <div class="abs locations-tag">LOCATIONS</div>
  <div class="abs back-brand">
    <div class="brand__mark"></div>
    LAKESHORE HEART CENTRE
  </div>

  <div class="abs site-heading" style="top:97px">LAKESHORE HEART CENTRE<br>&amp; DIAGNOSTIC CLINIC</div>
  <div class="abs map" style="top:135px" role="img" aria-label="Street map showing the Bayford clinic location"></div>
  <div class="abs site-info" style="top:160px">
    <svg width="16" height="24" viewBox="0 0 16 24"><path d="M8 0A8 8 0 0 0 0 8C0 14 8 24 8 24S16 14 16 8A8 8 0 0 0 8 0Z" fill="var(--red)"/><circle cx="8" cy="8" r="3.2" fill="#fff"/></svg>
    <div class="addr">1820 Maple Avenue<br>Suite 304, Bayford</div>
    <div class="city">BAYFORD<br>555-014-2290</div>
  </div>

  <div class="abs site-heading" style="top:320px;left:32px">LAKESHORE HEART CENTRE</div>
  <div class="abs map" style="top:346px;left:24px;width:238px" role="img" aria-label="Street map showing the Millbrook clinic location"></div>
  <div class="abs site-info" style="top:374px">
    <svg width="16" height="24" viewBox="0 0 16 24"><path d="M8 0A8 8 0 0 0 0 8C0 14 8 24 8 24S16 14 16 8A8 8 0 0 0 8 0Z" fill="var(--red)"/><circle cx="8" cy="8" r="3.2" fill="#fff"/></svg>
    <div class="addr">92 Harbour Street<br>North, Millbrook, ON</div>
    <div class="city" style="margin-top:20px">MILLBROOK<br>555-018-7716</div>
  </div>

  <div class="abs back-rule"></div>
</section>

</body>
</html>
```